Zestora - Landing Page

Need a landing page for a journal app. The app is based on a retrospective board, where each journal entry is split into 3 sections: "What went well", "What Didn't Go Well" and "Things To Try".
The landing page should match the style of all modern web application landing pages. Think Brint, Tivalo, Mirvane. I've included screenshots of the app.
One feature that I want to highlight that is not ready yet, is an AI coach. It will offer insights based on the history of the user's journal entries
1 page

```html
<!DOCTYPE html>
<html lang="en">
<head>
<meta charset="utf-8">
<title>Zestora – Journal App Landing Page</title>
<link href="https://fonts.googleapis.com/css2?family=Poppins:wght@500;600;700&family=Lato:wght@400;700&display=swap" rel="stylesheet">
<style>
:root{
  --purple:#5a55f0;
  --ink:#111320;
  --text:#2f3140;
  --muted:#6b6e7e;
  --lavender:#f6f5fe;
  --blue:#1cb5fd;
  --green:#2fe34b;
  --yellow:#fbbf0b;
  --sidebar:#1f2b3b;
  --pill:#4cc38a;
  --line:#e4e5ec;
  --footer:#f7f7f9;
}
*{box-sizing:border-box;margin:0;padding:0}
html,body{width:1200px;height:4275px;overflow:hidden}
body{position:relative;background:#fff;font-family:"Lato",sans-serif;color:var(--text)}
.abs{position:absolute}
h1,h2,h3,.logo,.btn{font-family:"Poppins",sans-serif}
.accent{color:var(--purple)}
.btn{position:absolute;display:flex;align-items:center;justify-content:center;background:var(--purple);color:#fff;border-radius:30px;font-weight:600;font-size:21px}

/* backgrounds */
.hero-bg{left:0;top:0;width:1200px;height:556px;background:var(--lavender)}
.hero-glow{left:0;top:0}
.wave{height:300px;background:linear-gradient(90deg,rgba(150,150,160,.0),rgba(150,150,160,.18),rgba(150,150,160,0));border-radius:50%}

/* nav */
.nav .logo{left:110px;top:28px;font-size:34px;font-weight:600;color:var(--ink)}
.nav .search{left:796px;top:42px}
.nav .login{left:842px;top:40px;font-size:15px;color:var(--muted)}
.nav .contact{left:918px;top:33px;width:116px;height:37px;font-size:15px}
.nav .menu{left:1056px;top:38px}

/* hero */
.hero-title{left:0;top:146px;width:1200px;text-align:center;font-size:55px;font-weight:600;color:var(--ink)}
.hero-lead{left:230px;top:236px;width:740px;text-align:center;font-size:17px;line-height:30px}
.hero-cta{left:515px;top:325px;width:171px;height:53px}
.partners{left:140px;top:430px;width:920px;display:flex;justify-content:space-between;align-items:center}
.partner{display:flex;align-items:center;gap:8px;font-family:"Poppins",sans-serif;font-weight:600;font-size:20px;color:#2e3142}
.partner i{display:block;width:16px;height:16px;background:var(--purple);border-radius:50%}

/* app mockup */
.app{position:absolute;background:#fff;border-radius:18px;box-shadow:0 10px 40px rgba(40,40,90,.12);overflow:hidden;display:flex}
.app .side{width:30px;background:var(--sidebar);display:flex;flex-direction:column;align-items:center;padding-top:14px;gap:12px;flex-shrink:0;position:relative}
.app .side b{display:block;width:9px;height:9px;border:1.5px solid #c9d0db;border-radius:2px}
.app .side b.on{background:var(--pill);border-color:var(--pill)}
.app .side .me{position:absolute;bottom:12px;width:12px;height:12px;border-radius:50%;background:#c9d0db}
.app .main{flex:1;position:relative;font-size:9px;color:#333}
.pill{display:inline-block;background:var(--pill);color:#fff;border-radius:10px;font-size:8px;padding:2px 9px}

.hero-app{left:161px;top:538px;width:876px;height:501px}
.hero-app .add{position:absolute;left:97px;top:43px;border:1px solid #cfd1da;border-radius:4px;padding:4px 10px;font-size:10px;font-weight:700}
.hero-app .pill{position:absolute;right:66px;top:46px}
.entry{position:absolute;left:97px;width:712px;border:1px solid var(--line);border-radius:4px;padding:16px 14px;font-size:9.5px;line-height:14.5px}
.entry h4{font-size:11px;margin-bottom:6px}
.entry .lbl{color:#8a8da0}
.entry .gap{margin-top:8px}
.entry.faded{opacity:.35}

.mini{width:478px;height:370px}
.mini .head{position:absolute;left:42px;top:12px;font-size:11px;font-weight:700}
.mini .date{position:absolute;left:72px;top:36px;font-size:8px;display:flex;gap:10px;align-items:center}
.cols{position:absolute;left:72px;top:66px;display:flex;gap:20px}
.col{width:166px;height:285px;flex-shrink:0;border:1px solid var(--line);border-radius:3px;padding:6px}
.col .ct{font-size:7.5px;font-weight:700;margin-bottom:10px}
.col .ct span{color:var(--purple)}
.editor{height:245px;border:1px solid var(--line);padding:4px}
.tools{font-size:7px;color:#555;border-bottom:1px solid var(--line);padding-bottom:4px;margin-bottom:6px;letter-spacing:2px}
.editor ul{padding-left:12px;font-size:7px;line-height:10px}

/* features */
.blob{position:absolute;border-radius:50%}
.feature h2{position:absolute;font-size:43px;font-weight:600;color:var(--ink)}
.feature p{position:absolute;width:430px;font-size:17.5px;line-height:33px}

/* ai coach */
.coach-title{left:0;top:2940px;width:1200px;text-align:center;color:#fff;font-size:50px;font-weight:600}
.coach-lead{left:240px;top:3030px;width:720px;text-align:center;color:#fff;font-size:17px;line-height:33px}
.coach-cta{left:521px;top:3162px;width:173px;height:54px;background:#fff;color:var(--purple)}

/* news */
.news-title{left:0;top:3345px;width:1200px;text-align:center;font-size:50px;font-weight:600;color:var(--ink)}
.news{left:108px;top:3456px;display:flex;gap:23px}
.card{width:227px;height:312px;background:#fff;box-shadow:0 4px 18px rgba(30,30,60,.09);padding:7px}
.card .photo{height:136px}
.card .tag{font-size:11px;color:var(--purple);margin:20px 3px 6px}
.card h3{font-size:14px;font-weight:600;line-height:21px;color:var(--ink);margin:0 3px}
.card .more{display:inline-block;margin:12px 3px 0;font-size:13px;font-weight:700;color:var(--purple);text-decoration:underline}

/* footer */
.footer{left:0;top:3851px;width:1200px;height:424px;background:var(--footer)}
.fcol{position:absolute;top:80px}
.fcol h4{font-family:"Poppins",sans-serif;font-size:19px;font-weight:600;color:var(--ink);margin-bottom:12px}
.fcol li{list-style:none;font-size:15px;color:#555866;line-height:36.5px}
.rule{left:111px;top:324px;width:978px;height:1px;background:#cfd0d8}
.copy{left:0;top:366px;width:1200px;text-align:center;font-size:15px;color:#333}
</style>
</head>
<body>

<div class="abs hero-bg"></div>
<svg class="abs hero-glow" width="1200" height="2500" viewBox="0 0 1200 2500">
  <defs>
    <linearGradient id="glow" x1="0" y1="940" x2="0" y2="1560" gradientUnits="userSpaceOnUse">
      <stop offset="0" stop-color="#f6f5fe"/><stop offset="1" stop-color="#ffffff"/>
    </linearGradient>
  </defs>
  <ellipse cx="600" cy="1700" rx="900" ry="760" fill="url(#glow)"/>
</svg>
<div class="abs wave" role="img" aria-label="Flowing grey line pattern" style="left:-40px;top:630px;width:210px"></div>
<div class="abs wave" role="img" aria-label="Flowing grey line pattern" style="left:1030px;top:610px;width:210px;height:220px"></div>

<header class="nav">
  <div class="abs logo">Zestora</div>
  <svg class="abs search" width="16" height="16" viewBox="0 0 16 16"><circle cx="6.5" cy="6.5" r="4.5" fill="none" stroke="#222" stroke-width="2"/><path d="M10 10l4 4" stroke="#222" stroke-width="2"/></svg>
  <div class="abs login">Log In</div>
  <div class="btn contact">Contact Us</div>
  <svg class="abs menu" width="31" height="24" viewBox="0 0 31 24"><path d="M0 2h31M8 12h23M0 22h31" stroke="#111" stroke-width="2.6"/></svg>
</header>

<h1 class="abs hero-title">Welcome to <span class="accent">Zestora</span></h1>
<p class="abs hero-lead">Lorem ipsum dolor sit amet, consectetur adipiscing elit, sed do eiusmod tempor incididunt ut m ad minim veniam, quis noris nisi ut aliquip ex ea commodo consequat.</p>
<div class="btn hero-cta">Get Started</div>

<div class="abs partners">
  <div class="partner"><i></i>Norvik</div>
  <div class="partner"><i></i>Baltrum</div>
  <div class="partner"><i></i>Corvella</div>
  <div class="partner"><i></i>Grendal</div>
  <div class="partner"><i></i>Dasoria</div>
</div>

<div class="app hero-app">
  <div class="side"><b class="on"></b><b></b><b></b><b></b><span class="me"></span></div>
  <div class="main">
    <div class="add">+ Add New</div>
    <span class="pill">Gym</span>
    <div class="entry" style="top:89px;height:320px">
      <h4>Thu Aug 22 2024</h4>
      <div class="lbl">What Went Well</div>
      <div class="gap">Completed all scheduled workouts this week.<br>Increased bench press weight by 10 pounds.<br>Maintained consistent energy levels throughout sessions.</div>
      <div class="lbl">What Didn't Go Well</div>
      <div class="gap">Struggled with form on deadlifts, leading to lower back discomfort.<br>Missed two stretching sessions after workouts.<br>Skipped meal prep, resulting in inconsistent nutrition.</div>
      <div class="lbl">Things To Try</div>
      <div class="gap">Focus on deadlift form by lowering the weight and reviewing proper technique.<br>Set reminders for post-workout stretching to prevent muscle tightness.<br>Dedicate Sunday evenings to meal prep to ensure a balanced diet.</div>
    </div>
    <div class="entry faded" style="top:421px;height:120px">
      <h4>Tue Aug 20 2024</h4>
      <div class="lbl">What Went Well</div>
      <div>Achieved a personal best in squats, adding 15 pounds.<br>Successfully integrated HIIT into cardio sessions.</div>
    </div>
  </div>
</div>

<!-- What went well -->
<section class="feature">
  <div class="blob" style="left:846px;top:1120px;width:500px;height:500px;background:var(--blue)"></div>
  <h2 style="left:111px;top:1188px">What went well</h2>
  <p style="left:111px;top:1254px">Lorem ipsum dolor sit amet, consectetur adipiscing elit, sed do eiusmod tempor incididunt ut labore et dolore magna aliqua. Ut enim ad minim veniam, quis laboris nisi ut aliquip ex ea commodo consequat.</p>
  <p style="left:111px;top:1418px">Duis aute irure dolor in reprehenderit in voluptate velit esse cillum dolore eu fugiat nulla pariatur.</p>
  <div class="btn" style="left:111px;top:1502px;width:173px;height:55px">Read More</div>
  <div class="app mini" style="left:613px;top:1195px">
    <div class="side"><b class="on"></b><b></b><b></b><b></b><span class="me"></span></div>
    <div class="main">
      <div class="head">Entry</div>
      <div class="date">▦ Thu Aug 22 2024 ⌄ <span class="pill">Gym</span></div>
      <div class="cols">
        <div class="col"><div class="ct"><span>▲</span> What Went Well?</div><div class="editor"><div class="tools">Normal ⌄ B I U S ❝ ≡ ≡</div><ul><li>Completed all scheduled workouts this week.</li><li>Increased bench press weight by 10 pounds.</li><li>Maintained consistent energy levels throughout sessions.</li></ul></div></div>
        <div class="col"><div class="ct"><span>▲</span> What Didn't Go Well?</div><div class="editor"><div class="tools">Normal ⌄ B I U S ❝ ≡ ≡</div><ul><li>Struggled with form on deadlifts, leading to lower back discomfort.</li><li>Missed two stretching sessions after workouts.</li><li>Skipped meal prep, resulting in inconsistent nutrition.</li></ul></div></div>
        <div class="col"><div class="ct"><span>▲</span> Things To Try</div><div class="editor"><div class="tools">Normal ⌄ B I U S</div><ul><li>Focus on form</li><li>Set reminders</li></ul></div></div>
      </div>
    </div>
  </div>
</section>

<!-- What didn't go well -->
<section class="feature">
  <div class="blob" style="left:-115px;top:1719px;width:496px;height:496px;background:var(--green)"></div>
  <div class="app mini" style="left:110px;top:1789px">
    <div class="side"><b class="on"></b><b></b><b></b><b></b><span class="me"></span></div>
    <div class="main">
      <div class="head">Entry</div>
      <div class="date">▦ Thu Aug 22 2024 ⌄ <span class="pill">Gym</span></div>
      <div class="cols">
        <div class="col"><div class="ct"><span>▲</span> What Went Well?</div><div class="editor"><div class="tools">Normal ⌄ B I U S ❝ ≡ ≡</div><ul><li>Completed all scheduled workouts this week.</li><li>Increased bench press weight by 10 pounds.</li><li>Maintained consistent energy levels throughout sessions.</li></ul></div></div>
        <div class="col"><div class="ct"><span>▲</span> What Didn't Go Well?</div><div class="editor"><div class="tools">Normal ⌄ B I U S ❝ ≡ ≡</div><ul><li>Struggled with form on deadlifts, leading to lower back discomfort.</li><li>Missed two stretching sessions after workouts.</li><li>Skipped meal prep, resulting in inconsistent nutrition.</li></ul></div></div>
        <div class="col"><div class="ct"><span>▲</span> Things To Try</div><div class="editor"><div class="tools">Normal ⌄ B I U S</div><ul><li>Focus on form</li><li>Set reminders</li></ul></div></div>
      </div>
    </div>
  </div>
  <h2 style="left:674px;top:1782px">What Didn't Go Well</h2>
  <p style="left:674px;top:1850px">Lorem ipsum dolor sit amet, consectetur adipiscing elit, sed do eiusmod tempor incididunt ut labore et dolore magna aliqua. Ut enim ad minim veniam, quis laboris nisi ut aliquip ex ea commodo consequat.</p>
  <p style="left:674px;top:2013px">Duis aute irure dolor in reprehenderit in voluptate velit esse cillum dolore eu fugiat nulla pariatur.</p>
  <div class="btn" style="left:674px;top:2098px;width:174px;height:55px">Read More</div>
</section>

<!-- Things to try -->
<section class="feature">
  <div class="blob" style="left:829px;top:2306px;width:500px;height:500px;background:var(--yellow)"></div>
  <h2 style="left:111px;top:2368px">Things To Try</h2>
  <p style="left:111px;top:2434px">Lorem ipsum dolor sit amet, consectetur adipiscing elit, sed do eiusmod tempor incididunt ut labore et dolore magna aliqua. Ut enim ad minim veniam, quis laboris nisi ut aliquip ex ea commodo consequat.</p>
  <p style="left:111px;top:2599px">Duis aute irure dolor in reprehenderit in voluptate velit esse cillum dolore eu fugiat nulla pariatur.</p>
  <div class="btn" style="left:111px;top:2684px;width:175px;height:55px">Read More</div>
  <div class="app mini" style="left:613px;top:2375px">
    <div class="side"><b class="on"></b><b></b><b></b><b></b><span class="me"></span></div>
    <div class="main">
      <div class="head">Entry</div>
      <div class="date">▦ Thu Aug 22 2024 ⌄ <span class="pill">Gym</span></div>
      <div class="cols">
        <div class="col"><div class="ct"><span>▲</span> What Went Well?</div><div class="editor"><div class="tools">Normal ⌄ B I U S ❝ ≡ ≡</div><ul><li>Completed all scheduled workouts this week.</li><li>Increased bench press weight by 10 pounds.</li><li>Maintained consistent energy levels throughout sessions.</li></ul></div></div>
        <div class="col"><div class="ct"><span>▲</span> What Didn't Go Well?</div><div class="editor"><div class="tools">Normal ⌄ B I U S ❝ ≡ ≡</div><ul><li>Struggled with form on deadlifts, leading to lower back discomfort.</li><li>Missed two stretching sessions after workouts.</li><li>Skipped meal prep, resulting in inconsistent nutrition.</li></ul></div></div>
        <div class="col"><div class="ct"><span>▲</span> Things To Try</div><div class="editor"><div class="tools">Normal ⌄ B I U S</div><ul><li>Focus on form</li><li>Set reminders</li></ul></div></div>
      </div>
    </div>
  </div>
</section>

<!-- AI coach -->
<svg class="abs" style="left:0;top:2892px" width="1200" height="390" viewBox="0 0 1200 390">
  <path d="M0 0H1200V220C1050 320 820 387 600 387S150 320 0 220Z" fill="var(--purple)"/>
</svg>
<h2 class="abs coach-title">AI coach</h2>
<p class="abs coach-lead">Lorem ipsum dolor sit amet, consectetur adipiscing elit, sed do eiusmod tempor incididunt ut ostrud exercitation ullamco te irure dolor in reprehenderit in voluptate velit esse cillum dolore at non proident, sunt in t mollit anim id est laborum.</p>
<div class="btn coach-cta">Get Started</div>

<!-- News -->
<h2 class="abs news-title">Latest <span class="accent">News</span></h2>
<div class="abs news">
  <article class="card">
    <div class="photo" role="img" aria-label="Business team meeting in a bright office" style="background:linear-gradient(135deg,#c9cdd3,#8e949c)"></div>
    <div class="tag">Webinar</div>
    <h3>Lorem ipsum dolor sit amet, consectetur, sed do eiusmod tempor incididunt et dolore magna aliqua</h3>
    <span class="more">Read More</span>
  </article>
  <article class="card">
    <div class="photo" role="img" aria-label="Two colleagues looking at a laptop together" style="background:linear-gradient(135deg,#4a5361,#1f2530)"></div>
    <div class="tag">Customer story</div>
    <h3>Amet, consectetur, sed do eiusmod tempor incididunt et dolore magna aliqua</h3>
    <span class="more">Read More</span>
  </article>
  <article class="card">
    <div class="photo" role="img" aria-label="Man working at a desk with a laptop" style="background:linear-gradient(135deg,#5b7389,#2c3a48)"></div>
    <div class="tag">Event</div>
    <h3>Lorem ipsum dolor sit amet, consectetur, sed do eiusmod tempor incididunt et dolore magna aliqua</h3>
    <span class="more">Read More</span>
  </article>
  <article class="card">
    <div class="photo" role="img" aria-label="Hand reviewing charts and documents" style="background:linear-gradient(135deg,#e3e7ec,#9aa6b2)"></div>
    <div class="tag">Customer story</div>
    <h3>Amet, consectetur, sed do eiusmod tempor incididunt et dolore magna aliqua</h3>
    <span class="more">Read More</span>
  </article>
</div>

<!-- Footer -->
<footer class="abs footer">
  <div class="fcol" style="left:111px"><h4>Solution</h4><ul><li>Business Professional</li><li>Team Leader / Principal</li><li>Procurement Director</li><li>Stuent / Professor</li></ul></div>
  <div class="fcol" style="left:345px"><h4>Industry</h4><ul><li>What went well</li><li>What Didn't Go Well</li><li>Things To Try</li></ul></div>
  <div class="fcol" style="left:607px"><h4>Features</h4><ul><li>Startup</li><li>Mid-Market</li><li>Enterprise</li></ul></div>
  <div class="fcol" style="left:795px"><h4>Resources</h4><ul><li>Get Support</li><li>Blog</li><li>Case Studies</li></ul></div>
  <div class="fcol" style="left:994px"><h4>Company</h4><ul><li>About Us</li><li>Careers</li><li>Contact Us</li></ul></div>
  <div class="abs rule"></div>
  <div class="abs copy">Copyrights@2024.Zestora.All Rights Reserved</div>
</footer>

</body>
</html>
```